Brightfield Ventures Inc. Letterhead

Creation of attractive and eye catching letterhead for a business start-up for the construction industry. Letterhead must relate to construction, but avoid standard hammer and tools in the design.

I forgot to add some details, sorry about that. Some pertinent info: Ph: 916-555-0187 brightfieldventures.example 448 Willowmere Ave, Ste 210 Folsom, CA 95999 info@brightfieldventures.example not sure if slogan should be in there" “Connecting construction professionals to create a purpose driven industry.” must be able to be used in word. Thanks!

```html
<!DOCTYPE html>
<html lang="en">
<head>
<meta charset="utf-8">
<title>Brightfield Ventures Inc. Letterhead</title>
<link href="https://fonts.googleapis.com/css2?family=Open+Sans:wght@400;600&family=Lato:wght@400;700&family=Montserrat:wght@700&display=swap" rel="stylesheet">
<style>
  :root {
    --brand-red: #b70a0c;
    --brand-navy: #101c54;
    --ink: #4a4a4a;
    --ink-dark: #333333;
    --paper: #ffffff;
  }
  * { margin: 0; padding: 0; box-sizing: border-box; }
  html, body { width: 1040px; height: 1200px; overflow: hidden; background: var(--paper); }
  .letterhead {
    position: relative;
    width: 1040px;
    height: 1200px;
    background: var(--paper);
    font-family: "Open Sans", Arial, sans-serif;
    color: var(--ink);
  }
  .top-band { position: absolute; top: 0; left: 0; }
  .brand {
    position: absolute;
    top: 112px;
    right: 100px;
    display: flex;
    align-items: center;
    gap: 14px;
  }
  .brand-mark { width: 22px; height: 22px; background: var(--brand-red); }
  .brand-name {
    font-family: "Montserrat", Arial, sans-serif;
    font-weight: 700;
    font-size: 24px;
    letter-spacing: 2px;
    color: var(--brand-navy);
    line-height: 1.2;
  }
  .letter-body {
    position: absolute;
    left: 97px;
    width: 842px;
    font-size: 16.5px;
  }
  .issue-date { top: 214px; }
  .recipient { top: 250px; line-height: 19px; }
  .salutation { top: 357px; }
  .message { top: 407px; }
  .message p {
    text-align: justify;
    hyphens: auto;
    line-height: 27px;
    margin-bottom: 26px;
  }
  .closing { top: 812px; }
  .signatory { top: 888px; }
  .signatory-name { font-size: 20px; color: var(--ink-dark); font-weight: 400; }
  .signatory-title { font-size: 16px; margin-top: 4px; }
  .contact-row {
    position: absolute;
    top: 1113px;
    left: 0;
    width: 1040px;
    text-align: center;
    font-family: "Lato", Arial, sans-serif;
    font-size: 18px;
    color: #222;
  }
  .contact-row .label { color: var(--brand-red); font-weight: 700; }
  .contact-row .sep { margin: 0 24px; }
  .contact-row .web { color: var(--brand-red); }
  .address-band {
    position: absolute;
    left: 0;
    bottom: 0;
    width: 1040px;
    height: 56px;
    background: var(--brand-navy);
    border-top: 2px solid #3a4677;
    color: #fff;
    font-family: "Lato", Arial, sans-serif;
    font-size: 18px;
    display: flex;
    align-items: center;
    justify-content: center;
  }
</style>
</head>
<body>
<div class="letterhead">
  <svg class="top-band" width="1040" height="40" viewBox="0 0 1040 40" aria-hidden="true">
    <polygon points="0,0 771,0 722,39 0,39" fill="var(--brand-red)"/>
  </svg>

  <div class="brand">
    <span class="brand-mark"></span>
    <span class="brand-name">BRIGHTFIELD VENTURES</span>
  </div>

  <div class="letter-body issue-date">Issuing Date: May 5, 2018</div>

  <div class="letter-body recipient">
    Name Of Employee Mr. XYZABC<br>
    Address of Employee<br>
    Address Line 2 etc..
  </div>

  <div class="letter-body salutation">Dear Mr.XYZABC</div>

  <div class="letter-body message">
    <p>Lorem Ipsum has been the industry's standard dummy text ever since the 1500s, when an unknown printer took a galley of type and scrambled it to make a type specimen book. It has survived not only five centuries, but also the leap into electronic typesetting, remaining essentially unchanged. It was popularised in the 1960s with the release of Typeline sheets containing Lorem Ipsum passages, and more recently with desktop publishing software like Pressmark Layout including versions of Lorem Ipsum.</p>
    <p>Lorem Ipsum is simply dummy text of the printing and typesetting industry. Lorem Ipsum has been the industry's standard dummy text ever since the 1500s, when an unknown printer took a galley of type and scrambled it to make a type specimen book.</p>
    <p>It has survived not only five centuries, but also the leap into electronic typesetting, remaining essentially unchanged. It was popularised in the 1960s with the release of Typeline sheets containing Lorem IpsumIpsum passages.</p>
  </div>

  <div class="letter-body closing">Yours Sincerely</div>

  <div class="letter-body signatory">
    <div class="signatory-name">Daniel Harper</div>
    <div class="signatory-title">Managing Director</div>
  </div>

  <div class="contact-row">
    <span class="label">P:</span> 916-555-0187<span class="sep">|</span><span class="label">E:</span> info@brightfieldventures.example<span class="sep">|</span><span class="web">www.brightfieldventures.example</span>
  </div>

  <div class="address-band">448 Willowmere Ave, Ste 210, Folsom, CA 95999</div>
</div>
</body>
</html>
```